Harbourline Electrical Solutions

On one side. LOGO (underneath:) Commercial Industrial Residential

- NAME & CONTACT DETAILS

Marcus T. Hollings
Project Manager

(Cell icon) (441) 555-0187
(Email icon) hlelectricalsolutions@mailvento.com
(Facebook & Instagram icons )@hlelectricalsolutions

Other side: LOGO - underneath ELECTRICAL CONSTRUCTION & MAINTENANCE . LED LIGHTING & AUTOMATION . LIFE SAFETY SYSTEMS (FIRE ALARM / SECURITY) . DATA & COMMUNICATION

```html
<!DOCTYPE html>
<html lang="en">
<head>
<meta charset="utf-8">
<title>Harbourline Electrical Solutions – Business Card</title>
<link rel="stylesheet" href="https://fonts.googleapis.com/css2?family=Montserrat:wght@400;500;600;700&display=swap">
<style>
  :root {
    --stage: #2a2a2d;
    --teal: #11566c;
    --teal-deep: #0d4a5e;
    --teal-faint: #0b4556;
    --ink: #2b2b2b;
    --ink-soft: #3c3c3c;
    --paper: #ffffff;
  }
  * { margin: 0; padding: 0; box-sizing: border-box; }
  html, body {
    width: 1200px; height: 1200px; overflow: hidden;
    background: var(--stage);
    font-family: "Montserrat", sans-serif;
  }
  .card {
    position: absolute;
    left: 300px;
    width: 600px;
    height: 360px;
  }

  /* Back side */
  .card-back { top: 220px; background: var(--teal); }
  .service-list {
    position: absolute; left: 50px; top: 148px;
    list-style: none;
    color: var(--paper);
    font-size: 11.2px; font-weight: 500;
    line-height: 18px;
  }
  .service-list li::before {
    content: ""; display: inline-block;
    width: 4px; height: 4px; border-radius: 50%;
    background: var(--paper);
    margin: 0 6px 2px 0; vertical-align: middle;
  }
  .vertical-name {
    position: absolute;
    left: 542px; top: 335px;
    transform: rotate(-90deg);
    transform-origin: left top;
    color: var(--teal-faint);
    font-size: 15px; font-weight: 500;
    letter-spacing: 3.2px;
    line-height: 18px;
    white-space: nowrap;
  }

  /* Front side */
  .card-front { top: 630px; background: var(--paper); }
  .brand {
    position: absolute; right: 48px; top: 34px;
    text-align: right;
  }
  .brand-name {
    color: var(--teal);
    font-size: 15.5px; font-weight: 600;
    letter-spacing: 2.4px; line-height: 17px;
  }
  .brand-sectors {
    margin-top: 22px;
    color: var(--ink);
    font-size: 9.4px; font-weight: 500;
    letter-spacing: 2.4px;
  }
  .brand-sectors .sep { color: var(--teal); margin: 0 3px; }

  .person {
    position: absolute; left: 46px; top: 244px;
  }
  .person-name {
    color: var(--teal);
    font-size: 17px; font-weight: 700;
    letter-spacing: 0.2px;
  }
  .person-role {
    color: var(--ink-soft);
    font-size: 11.5px; font-weight: 500;
    margin-top: -1px;
  }
  .person-rule {
    width: 49px; height: 2px; background: var(--teal);
    margin-top: 9px;
  }
  .contact {
    position: absolute; left: 46px; top: 299px;
    list-style: none;
    color: var(--ink);
    font-size: 12px; font-weight: 500;
    line-height: 19px;
  }
  .contact li { display: flex; align-items: center; gap: 4px; }
  .contact svg { width: 12px; height: 12px; flex: none; }
  .social {
    position: absolute; right: 50px; top: 318px;
    display: flex; align-items: center; gap: 6px;
    color: var(--ink);
    font-size: 12px; font-weight: 500;
    line-height: 19px;
  }
  .social-dot {
    width: 11px; height: 11px; border-radius: 50%;
    border: 1.2px solid var(--teal);
  }
</style>
</head>
<body>

<section class="card card-back">
  <ul class="service-list">
    <li>ELECTRICAL CONSTRUCTION &amp; MAINTENANCE</li>
    <li>LED LIGHTING &amp; AUTOMATION</li>
    <li>LIFE SAFETY SYSTEMS (FIRE ALARM / SECURITY)</li>
    <li>DATA &amp; COMMUNICATION</li>
  </ul>
  <div class="vertical-name">HARBOURLINE<br>ELECTRICAL<br>SOLUTIONS</div>
</section>

<section class="card card-front">
  <div class="brand">
    <div class="brand-name">HARBOURLINE<br>ELECTRICAL<br>SOLUTIONS</div>
    <div class="brand-sectors">COMMERCIAL<span class="sep">|</span>INDUSTRIAL<span class="sep">|</span>RESIDENTIAL</div>
  </div>

  <div class="person">
    <div class="person-name">MARCUS T. HOLLINGS</div>
    <div class="person-role">Project Manager</div>
    <div class="person-rule"></div>
  </div>

  <ul class="contact">
    <li>
      <svg viewBox="0 0 12 12" aria-hidden="true">
        <circle cx="6" cy="6" r="5.4" fill="none" stroke="#11566c" stroke-width="0.9"/>
        <path d="M4 3.3c.3-.2.6-.2.8.1l.5.8c.1.3 0 .5-.2.7l-.3.2c.3.7.8 1.2 1.5 1.5l.2-.3c.2-.2.5-.3.7-.2l.8.5c.3.2.3.5.1.8l-.3.4c-.3.3-.8.4-1.2.2C5.3 7.4 4.5 6.6 3.9 5.3c-.2-.4-.1-.9.2-1.2z" fill="#11566c"/>
      </svg>
      (441) 555-0187
    </li>
    <li>
      <svg viewBox="0 0 12 12" aria-hidden="true">
        <circle cx="6" cy="6" r="5.4" fill="none" stroke="#11566c" stroke-width="0.9"/>
        <rect x="3.3" y="4.1" width="5.4" height="3.8" fill="none" stroke="#11566c" stroke-width="0.8"/>
        <path d="M3.3 4.1 6 6.2 8.7 4.1" fill="none" stroke="#11566c" stroke-width="0.8"/>
      </svg>
      hlelectricalsolutions@mailvento.com
    </li>
  </ul>

  <div class="social">
    <span class="social-dot"></span>
    <span>@hlelectricalsolutions</span>
  </div>
</section>

</body>
</html>
```